Responsive web design for leading product search engine

Findnearby is the leading product search engine in Australia and is soon to expand into Asia. We need a lightweight responsive homepage designed for our 3 regional domains. Our domains are Findnearby.com, Findnearby.com.au and Findnearby.asia. We need 3 versions of the same page to appeal to each region. The page and images used need to use a responsive html 5 based web page. The images used in the design need to be responsive and include CSS3 style elements.

For inspiration I would divert you to www.brovanta.com and www.pelmiqo.com.au and I have attached a mockup of what I think it could look like.
Updates

Target Market(s)

Target market is female shoppers 16-40 years old

Industry/Entity Type

Retail

Coding

Coded - Design and coding required

Number of Pages Required

3 page

Colors
33b8a4

Requirements
Must have
• Different image for each of the 3 duplicate pages. 1 for each region Australia (.com.au) Asia (.asia) US (.com). These images must be licensed for public use.

```html
<!DOCTYPE html>
<html lang="en">
<head>
<meta charset="utf-8">
<title>Findnearby – Search products on sale at nearby stores</title>
<link rel="stylesheet" href="https://fonts.googleapis.com/css2?family=Open+Sans:wght@300;400;600;700&display=swap">
<style>
  :root{
    --teal:#33b8a4;
    --teal-dark:#2aa492;
    --ink:#3b3f44;
    --muted:#8a9096;
    --white:#ffffff;
    --hero-top:#7a6a58;
    --hero-bottom:#b59a7c;
  }
  *{box-sizing:border-box;margin:0;padding:0}
  html,body{width:763px;height:1200px;overflow:hidden}
  body{font-family:"Open Sans",Arial,sans-serif;color:var(--ink);background:var(--white);position:relative}

  /* Hero */
  .hero{position:absolute;left:0;top:0;width:763px;height:420px;
    background:linear-gradient(160deg,#5f5446 0%,var(--hero-top) 35%,var(--hero-bottom) 70%,#8c7a63 100%)}
  .hero-photo{position:absolute;inset:0}
  .site-header{position:absolute;left:0;top:0;width:100%;height:70px;display:flex;align-items:center;justify-content:space-between;padding:0 30px 0 34px}
  .brand{display:flex;align-items:center;gap:8px;color:var(--white);font-weight:600;font-size:26px;letter-spacing:-.3px}
  .brand-dot{width:26px;height:26px;border-radius:50%;background:var(--teal)}
  .header-tools{display:flex;gap:22px;align-items:center}
  .hero-title{position:absolute;top:172px;left:0;width:100%;text-align:center;color:var(--white);font-weight:300;font-size:30px;line-height:38px}
  .search-bar{position:absolute;top:254px;left:50%;transform:translateX(-50%);display:flex;gap:6px;height:30px}
  .search-field{width:200px;background:var(--white);border-radius:2px;font-size:10px;color:var(--muted);padding:0 10px;display:flex;align-items:center;justify-content:space-between}
  .search-field.location{width:150px}
  .search-btn{background:var(--teal);color:var(--white);font-size:10px;font-weight:600;padding:0 18px;display:flex;align-items:center;border-radius:2px;letter-spacing:.4px}
  .scroll-down{position:absolute;top:336px;left:50%;transform:translateX(-50%)}

  /* Discover */
  .device-visual{position:absolute;left:147px;top:453px;width:178px;height:203px;border-radius:12px;
    background:linear-gradient(180deg,#2b2d30,#1c1d1f)}
  .discover{position:absolute;left:381px;top:490px;width:300px}
  .discover h2{font-weight:400;font-size:24px;line-height:30px;color:var(--ink)}
  .discover p{margin-top:10px;font-size:10px;line-height:15px;color:var(--muted)}
  .btn{display:inline-block;margin-top:16px;background:var(--teal);color:var(--white);font-size:10px;font-weight:600;padding:8px 18px;border-radius:2px;letter-spacing:.3px}

  /* Services */
  .services-title{position:absolute;top:736px;width:100%;text-align:center;font-weight:300;font-size:24px;color:var(--ink)}
  .services{position:absolute;top:795px;left:0;width:100%}
  .service{position:absolute;width:170px;text-align:center}
  .service-icon{width:62px;height:62px;margin:0 auto;border-radius:50%;background:var(--teal);display:flex;align-items:center;justify-content:center}
  .service h3{margin-top:16px;font-size:10px;font-weight:700;color:var(--ink);letter-spacing:.3px}
  .service p{margin-top:7px;font-size:9px;line-height:13px;color:var(--muted)}

  /* Footer */
  .site-footer{position:absolute;left:0;top:974px;width:763px;height:226px;background:var(--teal);color:var(--white);text-align:center}
  .footer-brand{position:absolute;top:26px;left:50%;transform:translateX(-50%);display:flex;align-items:center;gap:8px;font-weight:600;font-size:26px}
  .footer-brand .brand-dot{background:var(--white)}
  .footer-nav{position:absolute;top:70px;width:100%;font-size:9px;line-height:22px}
  .footer-nav span{margin:0 9px}
  .footer-nav .sep{opacity:.7;margin:0}
  .store-badges{position:absolute;top:120px;left:50%;transform:translateX(-50%);display:flex;gap:8px}
  .store-badge{width:74px;height:24px;border-radius:4px;background:#111}
  .legal{position:absolute;top:160px;width:100%;font-size:8px;line-height:12px;opacity:.9}
</style>
</head>
<body>
  <section class="hero">
    <div class="hero-photo" role="img" aria-label="Photo of two smiling young women out shopping with bags in a sunlit street"></div>
    <header class="site-header">
      <div class="brand"><span class="brand-dot"></span>Findnearby</div>
      <div class="header-tools">
        <svg width="14" height="16" viewBox="0 0 14 16" aria-label="Account"><rect x="1" y="7" width="12" height="9" rx="1" fill="#fff"/><path d="M4 7V5a3 3 0 0 1 6 0v2" fill="none" stroke="#fff" stroke-width="2"/></svg>
        <svg width="16" height="14" viewBox="0 0 16 14" aria-label="Menu"><rect y="1" width="16" height="2" fill="#fff"/><rect y="6" width="16" height="2" fill="#fff"/><rect y="11" width="16" height="2" fill="#fff"/></svg>
      </div>
    </header>
    <h1 class="hero-title">Search millions of products on sale<br>at nearby stores</h1>
    <form class="search-bar">
      <div class="search-field">Search business or product <span>▾</span></div>
      <div class="search-field location">Current location <span>▾</span></div>
      <div class="search-btn">SEARCH NOW</div>
    </form>
    <svg class="scroll-down" width="40" height="40" viewBox="0 0 40 40" aria-label="Scroll down"><circle cx="20" cy="20" r="18" fill="none" stroke="#fff" stroke-width="1.5"/><path d="M12 17l8 8 8-8" fill="none" stroke="#fff" stroke-width="1.5"/></svg>
  </section>

  <div class="device-visual" role="img" aria-label="Tablet showing the Findnearby app with a product listing"></div>
  <section class="discover">
    <h2>Discover the best products<br>while you shop</h2>
    <p>Search every product in every store and you'll never miss out on the latest deal or sale in your area.</p>
    <span class="btn">LEARN MORE</span>
  </section>

  <h2 class="services-title">Our services</h2>
  <section class="services">
    <div class="service" style="left:80px">
      <div class="service-icon"><svg width="26" height="26" viewBox="0 0 26 26"><circle cx="11" cy="11" r="7" fill="none" stroke="#fff" stroke-width="2.5"/><path d="M16 16l7 7" stroke="#fff" stroke-width="3" stroke-linecap="round"/></svg></div>
      <h3>SEARCH PRODUCTS</h3>
      <p>Find the item you want in seconds across every shop near you today.</p>
    </div>
    <div class="service" style="left:296px">
      <div class="service-icon"><svg width="26" height="26" viewBox="0 0 26 26"><text x="13" y="21" text-anchor="middle" font-family="Open Sans, sans-serif" font-size="22" font-weight="700" fill="#fff">$</text></svg></div>
      <h3>COMPARE PRICES</h3>
      <p>See what each local store charges and pick the best price every time.</p>
    </div>
    <div class="service" style="left:505px">
      <div class="service-icon"><svg width="26" height="26" viewBox="0 0 26 26"><path d="M13 3l3 6.5 7 .8-5.2 4.8 1.4 7L13 18.6 6.8 22l1.4-7L3 10.3l7-.8z" fill="#fff"/></svg></div>
      <h3>ADD TO FAVORITES</h3>
      <p>Save the products you love and get told when they go on sale nearby.</p>
    </div>
  </section>

  <footer class="site-footer">
    <div class="footer-brand"><span class="brand-dot"></span>Findnearby</div>
    <nav class="footer-nav">
      <div><span>Findnearby for business</span><span class="sep">|</span><span>Why findnearby</span><span class="sep">|</span><span>FAQ</span><span class="sep">|</span><span>Contact us</span><span class="sep">|</span><span>Blog</span><span class="sep">|</span><span>Privacy policy</span></div>
      <div><span>Add new business</span><span class="sep">|</span><span>New user registration</span><span class="sep">|</span><span>Login</span></div>
    </nav>
    <div class="store-badges"><span class="store-badge"></span><span class="store-badge"></span></div>
    <p class="legal">© 2015 Findnearby.com<br>Store badges and marks belong to their owners.<br>Findnearby is not tied to them.</p>
  </footer>
</body>
</html>
```